Every Shelf Set Neatly or ESN Organized needs a business card design. ESN Organized is a professi

We need a business card design that is clean, sharp and conveys a sense of organization. I already have a logo.

Target Market(s)

Families (specifically mothers), small business owners, parents, seniors

Industry/Entity Type

Business

Contact Information for Business Card

My website is www.esnorganized-example.com and my Facebook page is http://www.sociallink-example.com/everyshelfsetneatly. The phone number is 418-552-7094 and I want to be listed as Lorna M. Pelham, Owner

Requirements
Must have
• My logo.

```html
<!DOCTYPE html>
<html lang="en">
<head>
<meta charset="utf-8">
<title>ESN Organized – Business Card</title>
<link rel="stylesheet" href="https://fonts.googleapis.com/css2?family=Montserrat:wght@400;500;700&display=swap">
<style>
  :root {
    --backdrop: #2a2a2a;
    --card-white: #ffffff;
    --card-black: #0b0b0b;
    --brand-blue: #1e88e5;
    --ink-dark: #1a1a1a;
    --ink-light: #ffffff;
    --ink-muted: #d8d8d8;
  }
  * { box-sizing: border-box; margin: 0; padding: 0; }
  html, body {
    width: 1200px;
    height: 950px;
    overflow: hidden;
    background: var(--backdrop);
    font-family: "Montserrat", Arial, sans-serif;
  }
  .stage {
    width: 1200px;
    height: 950px;
    display: flex;
    flex-direction: column;
    align-items: center;
    justify-content: center;
    gap: 50px;
  }
  .card {
    position: relative;
    width: 700px;
    height: 400px;
    border-radius: 6px;
    overflow: hidden;
  }
  .card--front { background: var(--card-white); }
  .card--back { background: var(--card-black); }

  .brand {
    display: flex;
    align-items: center;
    gap: 14px;
  }
  .brand__dot {
    width: 18px;
    height: 18px;
    border-radius: 50%;
    background: var(--brand-blue);
  }
  .brand__name {
    font-weight: 500;
    font-size: 40px;
    letter-spacing: 4px;
  }
  .card--front .brand__name { color: var(--ink-dark); }
  .card--back .brand__name { color: var(--ink-light); }

  .card--front .brand {
    position: absolute;
    left: 120px;
    top: 120px;
  }
  .front__web {
    position: absolute;
    left: 122px;
    top: 220px;
    font-size: 15px;
    letter-spacing: 7px;
    color: var(--ink-dark);
  }

  .card--back .brand {
    position: absolute;
    left: 250px;
    top: 70px;
  }
  .band {
    position: absolute;
    inset: 0;
  }
  .contacts {
    position: absolute;
    left: 34px;
    top: 200px;
    list-style: none;
    color: var(--ink-light);
    font-size: 17px;
    line-height: 28px;
  }
  .contacts li {
    display: flex;
    align-items: center;
    gap: 12px;
  }
  .contacts svg { width: 16px; height: 16px; flex: none; }
  .person {
    position: absolute;
    right: 60px;
    top: 310px;
    text-align: right;
    color: var(--ink-light);
    font-weight: 700;
  }
  .person__name { font-size: 24px; letter-spacing: 0.5px; }
  .person__role { font-size: 15px; margin-top: 6px; }
</style>
</head>
<body>
  <main class="stage">
    <section class="card card--front">
      <div class="brand">
        <span class="brand__dot"></span>
        <span class="brand__name">ESN Organized</span>
      </div>
      <p class="front__web">www.esnorganized-example.com</p>
    </section>

    <section class="card card--back">
      <svg class="band" viewBox="0 0 700 400" preserveAspectRatio="none" aria-hidden="true">
        <path d="M0,400 L0,195 Q0,165 35,165 L250,165 C320,165 320,275 395,275 L700,275 L700,400 Z" fill="var(--brand-blue)"/>
      </svg>

      <div class="brand">
        <span class="brand__dot"></span>
        <span class="brand__name">ESN Organized</span>
      </div>

      <ul class="contacts">
        <li>
          <svg viewBox="0 0 16 16" aria-hidden="true"><path d="M3 1.5 L6 1.5 L7 5 L5 6.2 C6 8.5 7.5 10 9.8 11 L11 9 L14.5 10 L14.5 13 C14.5 14 13.5 14.5 12.5 14.5 C6.5 14 2 9.5 1.5 3.5 C1.5 2.5 2 1.5 3 1.5 Z" fill="#fff"/></svg>
          418-552-7094
        </li>
        <li>
          <svg viewBox="0 0 16 16" aria-hidden="true"><circle cx="8" cy="8" r="6.5" fill="none" stroke="#fff" stroke-width="1.5"/><path d="M1.5 8 H14.5 M8 1.5 C5 5 5 11 8 14.5 M8 1.5 C11 5 11 11 8 14.5" fill="none" stroke="#fff" stroke-width="1.2"/></svg>
          www.esnorganized-example.com
        </li>
        <li>
          <svg viewBox="0 0 16 16" aria-hidden="true"><rect x="1.5" y="1.5" width="13" height="13" rx="2" fill="#fff"/></svg>
          everyshelfsetneatly
        </li>
      </ul>

      <div class="person">
        <p class="person__name">LORNA M. PELHAM</p>
        <p class="person__role">OWNER</p>
      </div>
    </section>
  </main>
</body>
</html>
```